New Webpage for High Class Expert Witness Services Company

We are looking for a minimalist design for a webpage that just has our logo and an entry form offer to connect with one of our Liaisons.
The entry form should just ask for Name, Email, Contact Info and Description of Project.

Company Name is: The Marlowe Crest Advisory Services

Number of Pages Required

1 page

```html
<!DOCTYPE html>
<html lang="en">
<head>
<meta charset="UTF-8">
<title>Marlowe Crest Advisory Services — Connect with a Liaison</title>
<link rel="stylesheet" href="https://fonts.googleapis.com/css2?family=Cinzel:wght@400;700&family=Marcellus&family=Roboto:wght@400&display=swap">
<style>
  :root {
    --bg: #2a2a2a;
    --bg-deep: #1f1f1f;
    --footer-bg: #252525;
    --rule: #3a3a3a;
    --text-light: #f2f2f2;
    --text-muted: #6e6e6e;
    --hero-dim: #a9a9a9;
    --hero-bright: #e6e6e6;
    --panel-border: #6a6a6a;
    --field-border: #bdbdbd;
    --footer-text: #8c8c8c;
    --gold-dark: #b8932e;
    --gold-mid: #d9bd62;
    --gold-light: #ecd98c;
    --ink: #1a1a1a;
  }
  * { box-sizing: border-box; margin: 0; padding: 0; }
  html, body {
    width: 1200px; height: 741px; overflow: hidden;
    background: var(--bg);
  }
  .page {
    position: relative; width: 1200px; height: 741px; overflow: hidden;
    background:
      radial-gradient(ellipse 520px 420px at 330px 240px, #363636 0%, rgba(54,54,54,0) 70%),
      linear-gradient(180deg, #2c2c2c 0%, var(--bg) 60%, var(--bg-deep) 100%);
  }
  .backdrop-emblem {
    position: absolute; left: 345px; top: 112px; width: 370px; height: 470px;
    background: radial-gradient(ellipse at 35% 20%, rgba(80,80,80,0.35) 0%, rgba(40,40,40,0.15) 55%, rgba(40,40,40,0) 80%);
  }
  .brand {
    position: absolute; left: 130px; top: 46px;
    display: flex; align-items: center; gap: 14px;
  }
  .brand-mark {
    width: 46px; height: 46px; background: #bfbfbf;
  }
  .brand-name {
    font-family: "Cinzel", serif; font-weight: 400;
    font-size: 23px; line-height: 26px; letter-spacing: 1px;
    color: #d4d4d4;
  }
  .phone {
    position: absolute; right: 106px; top: 38px;
    font-family: "Marcellus", serif; font-size: 33px; color: var(--text-light);
    letter-spacing: 0.5px;
  }
  .hero { position: absolute; left: 132px; top: 268px; }
  .hero-kicker {
    font-family: "Cinzel", serif; font-size: 18px; letter-spacing: 2.4px;
    color: var(--text-muted); margin-left: 4px;
  }
  .hero-title {
    margin-top: 8px;
    font-family: "Cinzel", serif; font-weight: 400; font-size: 51px;
    line-height: 57px; letter-spacing: 1.5px;
    background: linear-gradient(90deg, var(--hero-dim) 0%, var(--hero-bright) 100%);
    -webkit-background-clip: text; background-clip: text; color: transparent;
  }
  .liaison-panel {
    position: absolute; left: 715px; top: 121px; width: 380px; height: 439px;
    border: 1px solid var(--panel-border);
    background: radial-gradient(ellipse 340px 260px at 80% 95%, #3d3d3d 0%, #2a2a2a 60%, #242424 100%);
    padding: 36px 0 0 46px;
  }
  .panel-title {
    font-family: "Cinzel", serif; font-weight: 400; font-size: 21px;
    color: var(--text-light); letter-spacing: 0.5px;
  }
  .field {
    display: block; width: 296px; height: 42px; margin-top: 12px;
    border: 1px solid var(--field-border); background: transparent;
    font-family: "Roboto", sans-serif; font-size: 13.5px; color: var(--text-light);
    padding: 0 17px; line-height: 40px;
  }
  .field:first-of-type { margin-top: 25px; }
  .field-area { height: 89px; line-height: 1; padding-top: 13px; }
  .submit {
    display: flex; align-items: center; justify-content: center;
    width: 298px; height: 44px; margin-top: 13px;
    background: linear-gradient(100deg, var(--gold-dark) 0%, var(--gold-mid) 45%, var(--gold-light) 75%, var(--gold-mid) 100%);
    font-family: "Cinzel", serif; font-weight: 700; font-size: 16px; color: var(--ink);
    letter-spacing: 0.5px;
  }
  .site-footer {
    position: absolute; left: 0; top: 680px; width: 1200px; height: 61px;
    border-top: 1px solid var(--rule); background: var(--footer-bg);
    text-align: center;
    font-family: "Roboto", sans-serif; font-size: 12px; color: var(--footer-text);
    line-height: 58px;
  }
</style>
</head>
<body>
<div class="page">
  <div class="backdrop-emblem" role="img" aria-label="Faint embossed brand emblem in dark grey tones"></div>

  <header class="brand">
    <span class="brand-mark"></span>
    <span class="brand-name">The Marlowe Crest<br>Advisory Services</span>
  </header>
  <div class="phone">800-555-0142</div>

  <section class="hero">
    <p class="hero-kicker">MARLOWE CREST ADVISORY SERVICES</p>
    <h1 class="hero-title">SEAMLESS MEDICAL<br>EXPERT INTEGRATION</h1>
  </section>

  <form class="liaison-panel">
    <h2 class="panel-title">CONNECT WITH A LIAISON</h2>
    <div class="field">Name*</div>
    <div class="field">Email*</div>
    <div class="field">Phone number*</div>
    <div class="field field-area">Description of Project</div>
    <div class="submit">SUBMIT</div>
  </form>

  <footer class="site-footer">© 2026 The Marlowe Crest Advisory Services. All Rights Reserved</footer>
</div>
</body>
</html>
```